Business Card for Graphic Design Firm

This project is for a new graphic design firm based in New Jersey called Velmoria. We outsource graphic design and marketing jobs. We want to communicate that this is a professional company but it as well creative and artistic. This card may be used as a horizontal double sided paper card or a vertical single sided translucent card so feel free to submit designs in whichever format or both.
Updates

Reason: Extending the deadline because I'm not exactly satisfied with the designs so far.

Please view the updated project brief

Target Market(s)

Adults aged 25-60

Industry/Entity Type

Graphic Design

Font styles to use
Serif
Sans Serif

Requirements
Nice to have
• Maybe a triangular pattern around the edges similar to our logo

```html
<!DOCTYPE html>
<html lang="en">
<head>
<meta charset="utf-8">
<title>Velmoria Business Card</title>
<link rel="stylesheet" href="https://fonts.googleapis.com/css2?family=Montserrat:wght@500&family=Open+Sans:wght@400;600&display=swap">
<style>
  :root {
    --backdrop: #e9eaec;
    --card-front: #7d7e80;
    --card-back: #ffffff;
    --teal: #3a8fa3;
    --teal-light: #6fc9e4;
    --orange: #f6a623;
    --grey-text: #7a7b7d;
    --body-text: #6d6e70;
    --rule: #9a9b9d;
  }
  * { margin: 0; padding: 0; box-sizing: border-box; }
  html, body { width: 1200px; height: 600px; overflow: hidden; }
  body {
    background: var(--backdrop);
    position: relative;
    font-family: "Open Sans", Arial, sans-serif;
  }
  .card {
    position: absolute;
    top: 152px;
    width: 467px;
    height: 278px;
    overflow: hidden;
    box-shadow: 0 2px 6px rgba(0,0,0,0.12);
  }
  .card-front { left: 93px; background: var(--card-front); }
  .card-back { left: 638px; background: var(--card-back); }

  .edge-pattern {
    position: absolute;
    left: 0; top: 0;
    width: 330px; height: 278px;
    background:
      linear-gradient(90deg, rgba(246,166,35,0.55) 0%, rgba(58,143,163,0.35) 30%, rgba(125,126,128,0) 100%);
  }
  .wordmark {
    position: absolute;
    font-family: "Montserrat", Arial, sans-serif;
    font-weight: 500;
    font-size: 31px;
    letter-spacing: 3px;
    line-height: 1;
    text-transform: uppercase;
  }
  .card-front .wordmark { left: 244px; top: 232px; color: #ffffff; }
  .card-back .wordmark { left: 244px; top: 230px; color: var(--grey-text); }

  .faint-facets {
    position: absolute;
    right: 0; top: 0;
    width: 280px; height: 278px;
    background:
      linear-gradient(160deg, rgba(176,199,214,0.45) 0%, rgba(205,232,243,0.45) 45%, rgba(220,220,220,0.35) 70%, rgba(252,220,180,0.5) 100%);
  }

  .identity {
    position: absolute;
    right: 313px;
    top: 70px;
    text-align: right;
  }
  .person-name {
    font-weight: 600;
    font-size: 26px;
    line-height: 1;
    color: var(--teal);
  }
  .person-name .surname { color: var(--grey-text); }
  .person-role {
    font-size: 12px;
    color: var(--teal);
    margin-top: 2px;
  }
  .divider {
    position: absolute;
    left: 166px; top: 72px;
    width: 1px; height: 66px;
    background: var(--rule);
  }
  .contact-list {
    position: absolute;
    left: 176px; top: 70px;
    list-style: none;
    font-size: 12.5px;
    line-height: 17.5px;
    color: var(--body-text);
  }
  .contact-list li { display: flex; align-items: flex-start; }
  .contact-list svg { width: 10px; height: 10px; margin: 4px 7px 0 0; flex: none; fill: var(--teal); }
  .contact-list .address-line { padding-left: 17px; }
</style>
</head>
<body>

<section class="card card-front" aria-label="Card front">
  <div class="edge-pattern" role="img" aria-label="Fading triangular pattern in teal and orange along the left edge"></div>
  <div class="wordmark">Velmoria</div>
</section>

<section class="card card-back" aria-label="Card back">
  <div class="faint-facets" role="img" aria-label="Large faint triangular facets in pale blue, grey and orange"></div>

  <div class="identity">
    <div class="person-name">Liam <span class="surname">Carter</span></div>
    <div class="person-role">Manager / CEO</div>
  </div>
  <div class="divider"></div>

  <ul class="contact-list">
    <li>
      <svg viewBox="0 0 10 10"><path d="M1 4c0-2 1-3 4-3s4 1 4 3H7V3H3v1zM2 5h6l1 4H1z"/></svg>
      +61 3 9000 4127
    </li>
    <li>
      <svg viewBox="0 0 10 10"><path d="M0 2h10v6H0z M0 2l5 3.5L10 2" stroke="#fff" stroke-width="0.8"/></svg>
      info@velmoria.com
    </li>
    <li>
      <svg viewBox="0 0 10 10"><circle cx="5" cy="5" r="4.5"/><path d="M0.5 5h9M5 0.5v9M2 2.5h6M2 7.5h6" stroke="#fff" stroke-width="0.7" fill="none"/></svg>
      www.velmoria.com
    </li>
    <li>
      <svg viewBox="0 0 10 10"><path d="M5 0a3.5 3.5 0 0 1 3.5 3.5C8.5 6 5 10 5 10S1.5 6 1.5 3.5A3.5 3.5 0 0 1 5 0z"/><circle cx="5" cy="3.5" r="1.3" fill="#fff"/></svg>
      14 Halvern Street
    </li>
    <li class="address-line">Ashby VIC 3961</li>
  </ul>

  <div class="wordmark">Velmoria</div>
</section>

</body>
</html>
```